Construction company stationary design

We're wanting to develop a new professional stationary set for a newly establised property related business using our existing logo (attached). Business incorporates renovations, property investment and property development.

Specifically needing letter head, business cards, envelopes, email signature and need to get tshirt and caps embroydered.

Looking for something quite modern but professional using white, black and green.

Investment

```html
<!DOCTYPE html>
<html lang="en">
<head>
<meta charset="utf-8">
<title>Ridgeline Build – Business Card</title>
<link rel="stylesheet" href="https://fonts.googleapis.com/css2?family=Montserrat:wght@400;500;700&display=swap">
<style>
  :root {
    --green: #7dbb27;
    --green-dark: #6fa91f;
    --white: #ffffff;
    --paper: #f6f7f8;
    --ink: #6d6d72;
    --ink-strong: #55555a;
    --backdrop: #e7e6eb;
    --rule: #8a8a8f;
  }
  * { box-sizing: border-box; margin: 0; padding: 0; }
  html, body {
    width: 1200px;
    height: 934px;
    overflow: hidden;
    background: var(--backdrop);
    font-family: "Montserrat", sans-serif;
  }
  .card-set {
    position: absolute;
    top: 318px;
    left: 60px;
    display: flex;
    gap: 40px;
  }
  .card {
    position: relative;
    width: 520px;
    height: 297px;
    overflow: hidden;
  }

  /* Front face */
  .card--front {
    background: var(--green);
    color: var(--white);
  }
  .card--front .brand-name {
    position: absolute;
    left: 62px;
    top: 96px;
    display: flex;
    align-items: center;
    gap: 12px;
    font-size: 30px;
    font-weight: 700;
    letter-spacing: 0.5px;
    color: var(--white);
    text-transform: uppercase;
    line-height: 1;
  }
  .brand-mark {
    width: 18px;
    height: 18px;
    background: var(--white);
  }
  .card--front .web-address {
    position: absolute;
    left: 110px;
    bottom: 36px;
    font-size: 15px;
    letter-spacing: 0.4px;
  }
  .web-address strong { font-weight: 700; }

  /* Back face */
  .card--back {
    background: var(--paper);
    color: var(--ink);
  }
  .card--back .brand-name {
    position: absolute;
    left: 44px;
    top: 112px;
    display: flex;
    align-items: center;
    gap: 10px;
    font-size: 25px;
    font-weight: 700;
    color: var(--green);
    text-transform: uppercase;
    line-height: 1;
  }
  .card--back .brand-mark { background: var(--green); width: 15px; height: 15px; }
  .office-address {
    position: absolute;
    left: 60px;
    top: 196px;
    font-size: 12.5px;
    line-height: 1.35;
    color: var(--ink);
  }
  .divider {
    position: absolute;
    left: 318px;
    top: 150px;
    width: 1px;
    height: 26px;
    background: var(--rule);
  }
  .contact-block {
    position: absolute;
    left: 336px;
    top: 44px;
  }
  .person-name {
    font-size: 15px;
    font-weight: 700;
    color: var(--green);
    letter-spacing: 0.3px;
    text-transform: uppercase;
  }
  .person-title {
    font-size: 12px;
    margin: 4px 0 0 12px;
  }
  .contact-list {
    list-style: none;
    font-size: 11.5px;
    line-height: 1.3;
    margin-left: 30px;
  }
  .contact-list--phone { margin-top: 22px; }
  .contact-list--online { margin-top: 16px; }
  .contact-list .label { font-weight: 700; color: var(--ink-strong); }
  .accent-bar {
    position: absolute;
    right: 0;
    bottom: 30px;
    width: 190px;
    height: 13px;
    background: var(--green);
  }
</style>
</head>
<body>
  <main class="card-set">
    <section class="card card--front" aria-label="Business card front">
      <div class="brand-name"><span class="brand-mark"></span>Ridgeline Build</div>
      <p class="web-address">www.<strong>ridgelinebuild</strong>.com</p>
    </section>

    <section class="card card--back" aria-label="Business card back">
      <div class="brand-name"><span class="brand-mark"></span>Ridgeline Build</div>
      <address class="office-address" style="font-style:normal">
        214 Harrow Lane, Suite 8<br>
        Fairmont, CO 80000
      </address>
      <span class="divider"></span>
      <div class="contact-block">
        <h1 class="person-name">Jordan Ellery</h1>
        <p class="person-title">Chief Manager</p>
        <ul class="contact-list contact-list--phone">
          <li><span class="label">Phone:</span> (555) 310-7781</li>
          <li><span class="label">Fax:</span> (555) 310-7781</li>
        </ul>
        <ul class="contact-list contact-list--online">
          <li><span class="label">Email:</span> info@ridgelinebuild.com</li>
          <li><span class="label">Web:</span> www.ridgelinebuild.com</li>
        </ul>
      </div>
      <span class="accent-bar"></span>
    </section>
  </main>
</body>
</html>
```